Business card - Harbor Crest Builders

Design a business card utilizing the given logo.
colors we like: Black, greys, Teal, blues.
Tri color card, horizontal orientation likely
Logo and name likely best on top.
Info on card:

Dennis Farrow
#8 - 4815 Alder Ridge Blvd.
Surrey, B.C. V3K 2R9

778.555.0193
dennisfarrow@tellmail.ca

Slogan: "Building Dreams"

We are a construction company that specializes in new home construction on the West coast of BC Canada. Open Concepts designs of high end homes.

```html
<!DOCTYPE html>
<html lang="en">
<head>
<meta charset="utf-8">
<title>Harbor Crest Builders — Business Card</title>
<link rel="stylesheet" href="https://fonts.googleapis.com/css2?family=Didact+Gothic&family=Josefin+Sans:wght@700&display=swap">
<style>
  :root {
    --stage: #e4e4e2;
    --charcoal: #3c3d3f;
    --charcoal-deep: #2b2c2e;
    --black: #0d0d0e;
    --teal: #1f8a96;
    --teal-dark: #17707b;
    --paper: #ffffff;
    --paper-shade: #e9e9e9;
    --mist: #d2d2d2;
    --ink: #1d1d1f;
    --ink-soft: #3a3a3c;
  }
  * { box-sizing: border-box; margin: 0; padding: 0; }
  html, body { width: 1200px; height: 871px; overflow: hidden; }
  body {
    background: var(--stage);
    font-family: "Didact Gothic", "Century Gothic", sans-serif;
    position: relative;
  }
  .card {
    position: absolute;
    top: 287px;
    width: 520px;
    height: 297px;
    overflow: hidden;
    box-shadow: 0 6px 18px rgba(0,0,0,0.18);
  }
  /* Front side */
  .card-front {
    left: 60px;
    background: linear-gradient(160deg, var(--charcoal) 0%, var(--charcoal-deep) 100%);
  }
  .card-front .brand {
    position: absolute;
    top: 100px;
    left: 0;
    width: 100%;
    display: flex;
    justify-content: center;
    align-items: center;
    gap: 14px;
  }
  .brand-dot {
    width: 34px;
    height: 34px;
    border-radius: 50%;
    background: var(--black);
    flex: none;
  }
  .brand-name {
    font-size: 22px;
    letter-spacing: 2px;
    text-transform: uppercase;
    color: var(--black);
    white-space: nowrap;
  }
  .front-base { position: absolute; left: 0; bottom: 0; width: 520px; height: 297px; }
  .slogan {
    position: absolute;
    right: 40px;
    bottom: 18px;
    font-size: 15px;
    letter-spacing: 3px;
    color: var(--paper);
  }
  /* Back side */
  .card-back {
    left: 620px;
    background: linear-gradient(135deg, var(--paper-shade) 0%, var(--paper) 45%, var(--paper) 100%);
  }
  .back-shade {
    position: absolute;
    left: 0; top: 0;
    width: 200px; height: 297px;
    background: radial-gradient(circle at 40% 45%, var(--mist) 0%, rgba(210,210,210,0) 70%);
  }
  .holder-name {
    position: absolute;
    left: 22px;
    top: 118px;
    padding: 6px 14px;
    background: var(--paper);
    font-family: "Josefin Sans", "Century Gothic", sans-serif;
    font-weight: 700;
    font-size: 15px;
    letter-spacing: 2px;
    color: var(--ink);
  }
  .card-back .brand {
    position: absolute;
    top: 62px;
    right: 34px;
    display: flex;
    align-items: center;
    gap: 10px;
  }
  .card-back .brand-dot { width: 26px; height: 26px; }
  .card-back .brand-name { font-size: 16px; letter-spacing: 1.5px; }
  .contact {
    position: absolute;
    left: 272px;
    top: 140px;
    font-size: 13px;
    letter-spacing: 1.6px;
    line-height: 19px;
    color: var(--ink-soft);
    list-style: none;
  }
  .contact .address { margin-bottom: 16px; }
  .contact-line { display: flex; align-items: center; gap: 10px; }
  .contact-line svg { width: 11px; height: 11px; flex: none; }
</style>
</head>
<body>
  <section class="card card-front" aria-label="Business card front">
    <div class="brand">
      <span class="brand-dot"></span>
      <span class="brand-name">Harbor Crest Builders</span>
    </div>
    <svg class="front-base" viewBox="0 0 520 297" aria-hidden="true">
      <path d="M0,228 Q250,300 520,222 L520,297 L0,297 Z" fill="var(--black)"/>
      <path d="M0,246 Q250,304 520,236 L520,297 L0,297 Z" fill="var(--teal)"/>
    </svg>
    <p class="slogan">Building Dreams</p>
  </section>

  <section class="card card-back" aria-label="Business card back">
    <div class="back-shade"></div>
    <p class="holder-name">Dennis Farrow</p>
    <div class="brand">
      <span class="brand-dot"></span>
      <span class="brand-name">Harbor Crest Builders</span>
    </div>
    <ul class="contact">
      <li class="address">#8 - 4815 Alder Ridge Blvd.<br>Surrey, B.C. V3K 2R9</li>
      <li class="contact-line">
        <svg viewBox="0 0 12 12" aria-hidden="true"><path d="M1,4 Q6,0 11,4 L9,5 L8,4 L4,4 L3,5 Z M3,6 L9,6 L10,11 L2,11 Z" fill="var(--teal)"/></svg>
        778.555.0193
      </li>
      <li class="contact-line">
        <svg viewBox="0 0 12 12" aria-hidden="true"><rect x="1" y="2.5" width="10" height="7" fill="none" stroke="var(--teal)" stroke-width="1.2"/><path d="M1,2.5 L6,6.5 L11,2.5" fill="none" stroke="var(--teal)" stroke-width="1.2"/></svg>
        dennisfarrow@tellmail.ca
      </li>
    </ul>
  </section>
</body>
</html>
```